Dietitian needs awesome business card

I need a contemporary design that's eye catching but professional.
My card is to given to doctors, specialists and patients alike.
I manage patients with chronic diseases
I have uploaded my logo and current business card, I would also like the other Certified Clinical Nutritionist logo incorporated into the design

Target Market(s)

Doctors, specialists and patients

Industry/Entity Type

Healthcare

Contact Information for Business Card

www.brightfieldnutrition.com.au
Ph: 0427 561 903
Fax: 6457 2183
email: marcus.k.diet@fernmail.com
Space on the back of the card with: Appointment date, Appointment time and appointment location

Font styles to use
Serif

Colors
fbee3e
876aae
ffc214

Requirements
Must have
• My Logo
• Certified Clinical Nutritionist Logo
• My 4 locations - Pinebrook Medical Centre, North Corrin Health, Hollis Medical, Ashcombe Doctors Surgery
Nice to have
• I like the colours in my current business card

```html
<!DOCTYPE html>
<html lang="en">
<head>
<meta charset="utf-8">
<title>Brightfield Nutrition &amp; Dietetics – Business Card</title>
<link rel="stylesheet" href="https://fonts.googleapis.com/css2?family=Questrial&display=swap">
<style>
  :root{
    --bg:#e9eaec;
    --card:#ffffff;
    --navy:#1e3a9c;
    --blue-deep:#1a37a0;
    --blue-bright:#1f6fd0;
    --green:#8cc63f;
    --green-light:#b5dc3a;
    --orange:#f47a20;
    --rule:#9aa0a8;
    --ink:#3a3f47;
  }
  *{box-sizing:border-box;margin:0;padding:0}
  html,body{width:1200px;height:886px;overflow:hidden;background:var(--bg);
    font-family:"Questrial",sans-serif}
  .stage{position:relative;width:1200px;height:886px}
  .card{position:absolute;left:300px;width:600px;height:343px;background:var(--card);
    border-radius:22px;overflow:hidden;box-shadow:0 8px 24px rgba(0,0,0,.18)}
  .card--back{top:70px}
  .card--front{top:473px}

  /* back */
  .brand{position:absolute;left:36px;top:44px;display:flex;align-items:center;gap:12px}
  .brand__dot{width:44px;height:44px;border-radius:50%;background:var(--green)}
  .brand__name{color:var(--navy);font-size:22px;line-height:1.1}
  .badge{position:absolute;right:40px;top:28px;width:150px;height:56px;background:var(--orange);border-radius:3px}
  .rule{position:absolute;height:1px;background:var(--rule)}
  .field-label{position:absolute;color:var(--navy);font-size:18px}
  .ampm{position:absolute;right:40px;top:170px;color:var(--navy);font-size:13px}
  .locations{position:absolute;list-style:none;color:var(--ink);font-size:15px}
  .locations li{display:flex;align-items:center;gap:8px;margin-bottom:6px}
  .box{width:13px;height:13px;border:1.5px solid var(--navy)}

  /* front */
  .front-art{position:absolute;inset:0}
  .front-brand{position:absolute;left:48px;top:110px;display:flex;align-items:center;gap:12px}
  .contact{position:absolute;right:36px;top:150px;text-align:right;color:#fff;font-size:17px;line-height:1.35}
  .contact__name{color:var(--green-light);font-size:27px;margin-bottom:2px}
  .contact__role{font-size:19px;margin-bottom:12px}
</style>
</head>
<body>
<main class="stage">

  <section class="card card--back" aria-label="Appointment side">
    <div class="brand">
      <span class="brand__dot"></span>
      <span class="brand__name">Brightfield Nutrition &amp; Dietetics</span>
    </div>
    <div class="badge" role="img" aria-label="Certification badge"></div>

    <div class="rule" style="left:36px;right:40px;top:110px"></div>
    <div class="rule" style="left:36px;right:40px;top:140px"></div>
    <div class="rule" style="left:36px;right:40px;top:170px"></div>

    <span class="field-label" style="left:36px;top:220px">Date :</span>
    <div class="rule" style="left:94px;width:200px;top:238px"></div>
    <span class="field-label" style="left:316px;top:178px">Time :</span>
    <div class="rule" style="left:376px;right:96px;top:196px"></div>
    <span class="ampm">AM/PM</span>

    <ul class="locations" style="left:36px;top:262px">
      <li><span class="box"></span>Pinebrook Medical Centre</li>
      <li><span class="box"></span>North Corrin Health</li>
    </ul>
    <ul class="locations" style="left:316px;top:218px">
      <li><span class="box"></span>Ashcombe Doctors Surgery</li>
      <li><span class="box"></span>Hollis Medical</li>
    </ul>
  </section>

  <section class="card card--front" aria-label="Contact side">
    <svg class="front-art" viewBox="0 0 600 343" width="600" height="343" aria-hidden="true">
      <defs>
        <linearGradient id="panel" x1="0" y1="0" x2="1" y2="1">
          <stop offset="0" stop-color="var(--blue-bright)"/>
          <stop offset="1" stop-color="var(--blue-deep)"/>
        </linearGradient>
      </defs>
      <path d="M300 0 C285 160 170 270 0 300 L0 343 L600 343 L600 0 Z" fill="var(--green)"/>
      <path d="M318 0 C300 170 190 280 20 343 L600 343 L600 0 Z" fill="url(#panel)"/>
    </svg>
    <div class="front-brand">
      <span class="brand__dot"></span>
      <span class="brand__name">Brightfield</span>
    </div>
    <div class="contact">
      <p class="contact__name">Marcus Kellaway</p>
      <p class="contact__role">Nutritionist &amp; Chef</p>
      <p>P. 0427 561 903</p>
      <p>F. 6457 2183</p>
      <p>marcus.k.diet@fernmail.com</p>
      <p>brightfieldnutrition.com.au</p>
    </div>
  </section>

</main>
</body>
</html>
```